Stylish business cards for KV7

To create an appealing and professional business card design for a WOMEN Owned Construction Supply Company.
2 sided card. Incorporate brand elements, curvy, colorful, sleek and bright. No solid white background. attached samples of styles added shapes/ribbons. Want something with that WOW that looks awesome, factor. It is a new logo, so feel free to mess with logo colors in the blue and teal factors that can look good with both dark and light background. If you want to try a watermark with just the KV7, without the "Supply" that might look cool to.

Industry/Entity Type

Women owned construction supply company

Contact Information for Business Card

Name, Title, and phone number and email, web page. maybe spot for qr code.

Font styles to use
Sans Serif

Requirements
Nice to have
• would love to see colors, maybe stylish ribbon dividers or some sort of 2 or 3 tone color card that compliments logo.
Should not have
• Please do not have all white background. Do not include Home/reale state/ or building images.

```html
<!DOCTYPE html>
<html lang="en">
<head>
<meta charset="UTF-8">
<title>KV7 Supply — Business Cards</title>
<link href="https://fonts.googleapis.com/css2?family=Poppins:wght@400;500;600;700&display=swap" rel="stylesheet">
<style>
  :root {
    --bg: #2a2a2c;
    --navy: #1d3a66;
    --navy-deep: #1c3559;
    --teal: #2a9fc6;
    --teal-mid: #236f96;
    --white: #ffffff;
    --paper-tint: #e8f2f8;
    --divider: #4a6a8a;
    --text-dark: #1d2f4d;
    --icon: #2a9fc6;
  }
  * { box-sizing: border-box; margin: 0; padding: 0; }
  html, body {
    width: 1200px;
    height: 875px;
    overflow: hidden;
    background: var(--bg);
    font-family: "Poppins", sans-serif;
  }
  .sheet {
    width: 1200px;
    height: 875px;
    display: flex;
    align-items: center;
    justify-content: center;
    gap: 40px;
  }
  .card {
    width: 540px;
    height: 309px;
    border-radius: 22px;
    position: relative;
    overflow: hidden;
    box-shadow: 0 14px 34px rgba(0,0,0,0.45);
  }
  .card-front {
    background: radial-gradient(ellipse at 52% 42%, var(--teal) 0%, var(--teal-mid) 38%, var(--navy-deep) 82%);
    display: flex;
    align-items: center;
    justify-content: center;
  }
  .brand-front {
    color: var(--white);
    font-weight: 600;
    font-size: 60px;
    letter-spacing: 1px;
    white-space: nowrap;
    display: flex;
    align-items: center;
    gap: 14px;
  }
  .brand-mark {
    width: 16px;
    height: 16px;
    border-radius: 50%;
    background: currentColor;
    flex: none;
  }
  .card-back {
    background: linear-gradient(135deg, var(--white) 0%, var(--white) 45%, var(--paper-tint) 100%);
    display: flex;
    align-items: center;
  }
  .ribbon {
    position: absolute;
    left: 0;
    bottom: 0;
    width: 540px;
    height: 70px;
  }
  .ribbon-navy { fill: var(--navy); }
  .ribbon-teal { fill: var(--teal); }
  .brand-back {
    position: relative;
    width: 258px;
    padding-left: 36px;
    padding-bottom: 20px;
    color: var(--navy);
    font-weight: 600;
    font-size: 30px;
    white-space: nowrap;
    display: flex;
    align-items: center;
    gap: 10px;
  }
  .brand-back .brand-mark { width: 11px; height: 11px; }
  .divider {
    position: relative;
    width: 1px;
    height: 150px;
    background: var(--divider);
    margin-right: 34px;
    margin-bottom: 20px;
  }
  .contact { position: relative; color: var(--text-dark); margin-bottom: 20px; }
  .contact-name {
    font-weight: 700;
    font-size: 17px;
    color: var(--navy);
    letter-spacing: 0.3px;
    line-height: 1.1;
  }
  .contact-title { font-size: 11.5px; margin-bottom: 8px; }
  .contact-address { font-size: 11.5px; line-height: 1.35; margin-bottom: 10px; }
  .contact-list { list-style: none; font-size: 11.5px; line-height: 1.5; }
  .contact-list li { display: flex; align-items: center; gap: 8px; }
  .contact-list svg { width: 10px; height: 10px; fill: var(--icon); flex: none; }
</style>
</head>
<body>
  <main class="sheet">
    <section class="card card-front" aria-label="Card front">
      <div class="brand-front"><span class="brand-mark"></span>KV7 Supply</div>
    </section>

    <section class="card card-back" aria-label="Card back">
      <svg class="ribbon" viewBox="0 0 540 70" preserveAspectRatio="none" aria-hidden="true">
        <path class="ribbon-teal" d="M0 46 C140 20 300 62 540 18 L540 70 L0 70 Z"/>
        <path class="ribbon-navy" d="M0 58 C160 36 330 72 540 34 L540 70 L0 70 Z"/>
      </svg>
      <div class="brand-back"><span class="brand-mark"></span>KV7 Supply</div>
      <div class="divider"></div>
      <div class="contact">
        <p class="contact-name">DANIEL REYES</p>
        <p class="contact-title">General Manager</p>
        <p class="contact-address">48 Foundry Square<br>Brookfield, NJ 07000 USA</p>
        <ul class="contact-list">
          <li><svg viewBox="0 0 10 10"><path d="M2 0.5 L3.6 2.6 L2.8 3.6 Q4 5.8 6.4 7.2 L7.4 6.4 L9.5 8 L8.4 9.5 Q4.5 9.3 0.5 1.6 Z"/></svg>+1.555.014.2290</li>
          <li><svg viewBox="0 0 10 10"><path d="M0.5 2 H9.5 V8 H0.5 Z M0.5 2 L5 5.5 L9.5 2" fill="none" stroke="#2a9fc6" stroke-width="1.2"/></svg>name@kv7supply.com</li>
          <li><svg viewBox="0 0 10 10"><circle cx="5" cy="5" r="4.3" fill="none" stroke="#2a9fc6" stroke-width="1.1"/><path d="M0.7 5 H9.3 M5 0.7 Q2.4 5 5 9.3 M5 0.7 Q7.6 5 5 9.3" fill="none" stroke="#2a9fc6" stroke-width="0.9"/></svg>www.kv7supply.com</li>
        </ul>
      </div>
    </section>
  </main>
</body>
</html>
```